Need Flyer for Our Real estate Agency

Need to run General Campaign for our agency with Start of New Year as our theme ..Must have an agent's picture on the DL..
Address:
27 / 486Brindle rd, Marsden VIC 3047
Ph:03 9412 7306
email:info@kovalinrealestate.com.au
www.kovalinrealestate.com.au
Something like as attached picture..
Target Market(s)
Home Buyers
Industry/Entity Type
Real Estate Agent
Requirements
Must have
- Our Logo Colours

```html
<!DOCTYPE html>
<html lang="en">
<head>
<meta charset="utf-8">
<title>Kovalin Real Estate – DL Flyer</title>
<link rel="stylesheet" href="https://fonts.googleapis.com/css2?family=Lato:wght@300;400;700;900&display=swap">
<style>
  :root {
    --backdrop: #d4d5d7;
    --navy-deep: #06154a;
    --navy-mid: #0e2466;
    --navy-light: #1a3479;
    --burgundy: #7b1420;
    --white: #ffffff;
    --curve-grey: #c9cbd0;
    --photo-sky: #aebdd4;
    --photo-house: #8c8f93;
    --photo-lawn: #4f7a3a;
    --photo-suit: #2f4f86;
    --photo-dark: #1d2a3f;
    --photo-house-red: #d8534f;
  }
  html, body {
    margin: 0;
    padding: 0;
    width: 1200px;
    height: 1191px;
    overflow: hidden;
    background: var(--backdrop);
    font-family: "Lato", Arial, sans-serif;
  }
  .flyer-sheet {
    position: relative;
    width: 1200px;
    height: 1191px;
  }
  .flyer-side {
    position: absolute;
    left: 54px;
    width: 1065px;
    height: 508px;
    display: block;
    filter: drop-shadow(0 10px 10px rgba(0, 0, 0, 0.28));
  }
  .flyer-side--front { top: 52px; }
  .flyer-side--back { top: 637px; }
  .brand-name {
    font-family: "Lato", Arial, sans-serif;
    font-weight: 400;
    fill: var(--white);
    letter-spacing: 4px;
  }
  .headline {
    font-weight: 300;
    fill: var(--white);
    font-size: 25px;
  }
  .tagline {
    font-weight: 400;
    fill: var(--white);
    font-size: 12.5px;
  }
  .tagline-strong { font-weight: 900; }
  .call-button-text {
    font-weight: 900;
    fill: var(--burgundy);
    font-size: 17px;
  }
  .band-note {
    font-weight: 400;
    fill: var(--white);
    font-size: 14px;
  }
  .agent-title {
    font-weight: 400;
    fill: var(--white);
    font-size: 17px;
  }
  .contact-line {
    font-weight: 400;
    fill: var(--white);
    font-size: 15px;
  }
  .office-address {
    font-weight: 400;
    fill: var(--white);
    font-size: 15px;
  }
  .icon-ring { fill: none; stroke: var(--white); stroke-width: 1.4; }
  .icon-mark { fill: var(--white); }
</style>
</head>
<body>
<main class="flyer-sheet">

  <!-- Front side -->
  <svg class="flyer-side flyer-side--front" viewBox="0 0 827 395" preserveAspectRatio="none" aria-label="Kovalin Real Estate flyer front">
    <defs>
      <linearGradient id="front-photo-tone" x1="0" y1="0" x2="0" y2="1">
        <stop offset="0" stop-color="var(--photo-sky)"/>
        <stop offset="0.45" stop-color="var(--photo-house)"/>
        <stop offset="0.7" stop-color="var(--photo-suit)"/>
        <stop offset="1" stop-color="var(--photo-lawn)"/>
      </linearGradient>
      <linearGradient id="front-panel-tone" x1="0" y1="0" x2="1" y2="0">
        <stop offset="0" stop-color="var(--navy-light)"/>
        <stop offset="0.5" stop-color="var(--navy-mid)"/>
        <stop offset="1" stop-color="var(--navy-deep)"/>
      </linearGradient>
      <clipPath id="front-panel-shape">
        <path d="M268 0 L827 0 L827 395 L330 395 Q385 200 268 0 Z"/>
      </clipPath>
    </defs>

    <rect class="agent-photo" x="0" y="0" width="360" height="395" fill="url(#front-photo-tone)" role="img" aria-label="Photo of the smiling agent in a blue suit standing before a large family home"/>

    <path d="M236 0 L300 0 Q395 200 330 395 L316 395 Q378 200 236 0 Z" fill="var(--curve-grey)"/>
    <path d="M250 0 L300 0 Q398 200 334 395 L322 395 Q385 200 250 0 Z" fill="var(--white)"/>

    <g clip-path="url(#front-panel-shape)">
      <rect x="250" y="0" width="577" height="395" fill="url(#front-panel-tone)"/>
      <rect x="250" y="334" width="577" height="2.5" fill="var(--white)"/>
      <rect x="250" y="338" width="577" height="57" fill="var(--burgundy)"/>
    </g>

    <text class="brand-name" x="600" y="148" text-anchor="middle" font-size="46">KOVALIN</text>

    <text class="headline" x="600" y="211" text-anchor="middle">Curios to know what your</text>
    <text class="headline" x="600" y="249" text-anchor="middle">home is worth?</text>

    <text class="tagline" x="600" y="292" text-anchor="middle">START THE NEW YEAR WITH <tspan class="tagline-strong">RAVI DHILLON</tspan> AND FIND OUT!</text>

    <rect class="call-button" x="446" y="320" width="310" height="38" rx="19" fill="var(--white)"/>
    <text class="call-button-text" x="462" y="345">CALL ME NOW!</text>
    <g class="phone-icon" transform="translate(598 339)">
      <circle class="icon-ring" r="7.5" stroke="var(--burgundy)" style="stroke: var(--burgundy)"/>
      <path d="M-3.5 -3.5 Q-4 1 0 3.8 L1.8 4.2 L3.3 2.4 L1.6 1 L0.5 1.8 Q-1.5 0.4 -1.8 -1.4 L-1 -2.3 L-2.2 -4.2 Z" fill="var(--burgundy)"/>
    </g>
    <text class="call-button-text" x="613" y="345">0412 508 963</text>

    <text class="band-note" x="600" y="380" text-anchor="middle">For Free property Appraisal</text>
  </svg>

  <!-- Back side -->
  <svg class="flyer-side flyer-side--back" viewBox="0 0 827 395" preserveAspectRatio="none" aria-label="Kovalin Real Estate flyer back">
    <defs>
      <radialGradient id="back-photo-tone" cx="0.35" cy="0.55" r="0.7">
        <stop offset="0" stop-color="var(--photo-house-red)"/>
        <stop offset="0.4" stop-color="#b98a78"/>
        <stop offset="1" stop-color="var(--photo-dark)"/>
      </radialGradient>
      <linearGradient id="back-panel-tone" x1="0" y1="0" x2="1" y2="0">
        <stop offset="0" stop-color="var(--navy-light)"/>
        <stop offset="0.5" stop-color="var(--navy-mid)"/>
        <stop offset="1" stop-color="var(--navy-deep)"/>
      </linearGradient>
      <clipPath id="back-panel-shape">
        <path d="M268 0 L827 0 L827 395 L330 395 Q385 200 268 0 Z"/>
      </clipPath>
    </defs>

    <rect class="home-photo" x="0" y="0" width="360" height="395" fill="url(#back-photo-tone)" role="img" aria-label="Photo of two hands sheltering a small red model house"/>

    <path d="M236 0 L300 0 Q395 200 330 395 L316 395 Q378 200 236 0 Z" fill="var(--curve-grey)"/>
    <path d="M250 0 L300 0 Q398 200 334 395 L322 395 Q385 200 250 0 Z" fill="var(--white)"/>

    <g clip-path="url(#back-panel-shape)">
      <rect x="250" y="0" width="577" height="395" fill="url(#back-panel-tone)"/>
      <rect x="250" y="334" width="577" height="2.5" fill="var(--white)"/>
      <rect x="250" y="338" width="577" height="57" fill="var(--burgundy)"/>
    </g>

    <text class="brand-name" x="600" y="148" text-anchor="middle" font-size="46">KOVALIN</text>

    <text class="agent-title" x="475" y="204">Ravi Dhillon, Director</text>

    <g class="contact-list">
      <g class="phone-icon" transform="translate(483 234)">
        <circle class="icon-ring" r="7"/>
        <path class="icon-mark" d="M-3.3 -3.3 Q-3.8 1 0 3.6 L1.7 4 L3.1 2.3 L1.5 1 L0.5 1.7 Q-1.4 0.4 -1.7 -1.3 L-1 -2.2 L-2.1 -4 Z"/>
      </g>
      <text class="contact-line" x="499" y="239">03 9412 7306</text>

      <g class="mail-icon" transform="translate(483 264)">
        <circle class="icon-mark" r="7"/>
        <rect x="-4" y="-2.8" width="8" height="5.6" fill="var(--navy-mid)"/>
        <path d="M-4 -2.8 L0 0.6 L4 -2.8" fill="none" stroke="var(--white)" stroke-width="0.9"/>
      </g>
      <text class="contact-line" x="499" y="269">ravi.dhillon@kovalinrealestate.com.au</text>

      <g class="web-icon" transform="translate(483 295)">
        <circle class="icon-ring" r="7"/>
        <ellipse cx="0" cy="0" rx="2.8" ry="5" fill="none" stroke="var(--white)" stroke-width="0.9"/>
        <line x1="-5" y1="0" x2="5" y2="0" stroke="var(--white)" stroke-width="0.9"/>
      </g>
      <text class="contact-line" x="499" y="300">www.kovalinrealestate.com.au</text>
    </g>

    <text class="office-address" x="603" y="370" text-anchor="middle">27/486 Brindle Rd Marsden, Victoria, Australia 3047</text>
  </svg>

</main>
</body>
</html>
```